Kelvaro.ch is looking for business card letterhead and envelope C5 with WOW effect

We need a strong business card for our company Kelvaro.ch, logo is available. You want a black or dark background on which the logo Stark r% 26 # 252; appears. Letterhead and envelope in C5 format should be in a similar design, but does not have to be We need a strong business card for our company Kelvaro.ch, logo is available. A black or dark background is desired, on which the logo Stark comes across. The letterhead and the envelope in C5 format should have a similar design.

Target Market(s)

Private customers as well as entrepreneurs

Contact Information for Business Card

E-mail: info@kelvaro-example.ch
Web.www.Kelvaro-example.ch
Tel: +41 ( 0 ) 79 482 6037
Adresse:
Lindenweg 14
9406 Tarnbach

Hier kann man Icons verwenden für Email,Tel und Adressse

Font styles to use
Other font styles liked:
• Dubai,bold

Colors

Designer to choose colors to be used in the design.

Requirements
Must have
• WOW effect
Nice to have
• R% 26 # 252; back business card with our service listings. - VEHICLE LABELING - SHOP WINDOW LABELING - STICKERS AND MUCH MORE ... in red color

```html
<!DOCTYPE html>
<html lang="en">
<head>
<meta charset="utf-8">
<title>Kelvaro.ch – Business Card</title>
<link href="https://fonts.googleapis.com/css2?family=Exo+2:wght@500;600;800&display=swap" rel="stylesheet">
<style>
  :root {
    --backdrop: #8a5a33;
    --card-yellow: #fdcb1c;
    --card-dark: #1f1f1f;
    --ink: #1a1a1a;
    --white: #ffffff;
    --accent: #fdcb1c;
  }
  * { margin: 0; padding: 0; box-sizing: border-box; }
  html, body {
    width: 1200px;
    height: 900px;
    overflow: hidden;
    background: var(--backdrop);
    font-family: "Exo 2", sans-serif;
  }
  .canvas {
    position: relative;
    width: 1200px;
    height: 900px;
  }
  .card {
    position: absolute;
    box-shadow: 4px 5px 8px rgba(0, 0, 0, 0.45);
  }
  .card--front {
    left: 329px; top: 90px;
    width: 556px; height: 343px;
    background: var(--card-yellow);
    color: var(--ink);
  }
  .card--back {
    left: 330px; top: 469px;
    width: 560px; height: 343px;
    background: var(--card-dark);
  }
  .brand-name {
    position: absolute;
    font-weight: 800;
    text-transform: uppercase;
    letter-spacing: 1px;
    white-space: nowrap;
  }
  .card--front .brand-name {
    left: 0; right: 0; top: 104px;
    text-align: center;
    font-size: 46px;
    color: var(--ink);
  }
  .contact {
    position: absolute;
    left: 0; right: 0; top: 220px;
    text-align: center;
    font-weight: 600;
    font-size: 19px;
    line-height: 26px;
  }
  .contact__rule {
    width: 180px;
    height: 1px;
    margin: 8px auto 6px;
    background: var(--ink);
    opacity: 0.6;
  }
  .brand-mark {
    position: absolute;
    left: 150px; top: 110px;
    width: 42px; height: 42px;
    background: var(--accent);
  }
  .card--back .brand-name {
    left: 225px; top: 130px;
    font-size: 32px;
    color: var(--white);
  }
  .services {
    position: absolute;
    left: 0; right: 0; top: 270px;
    text-align: center;
    font-weight: 600;
    font-size: 15.5px;
    line-height: 22px;
    color: var(--accent);
    text-transform: uppercase;
  }
</style>
</head>
<body>
<main class="canvas">
  <section class="card card--front">
    <div class="brand-name">Kelvaro.ch</div>
    <div class="contact">
      <p class="contact__line">P: +41 ( 0 ) 79 482 6037 | E: info@kelvaro-example.ch</p>
      <p class="contact__line">W: www.Kelvaro-example.ch</p>
      <div class="contact__rule"></div>
      <p class="contact__line">Lindenweg 14, 9406 Tarnbach</p>
    </div>
  </section>

  <section class="card card--back">
    <div class="brand-mark"></div>
    <div class="brand-name">Kelvaro.ch</div>
    <div class="services">
      <p>Vehicle labeling | Shop window labeling</p>
      <p>Stickers and much more ...</p>
    </div>
  </section>
</main>
</body>
</html>
```